Business Card for Field Bloom-Eco Friendly Organic Clothing Brand

We are looking for an amazing business card for our eco friendly, organic clothing brand. We are thinking maybe a business card with a peel off sticker on the back, since our hanging clothing tag is a peel off sticker on the back. I will attach our hang tag so we can make sure we stay in line with our design. I've also attached a bag we are doing because I do like the scattered emblem look as well.

```html
<!DOCTYPE html>
<html lang="en">
<head>
<meta charset="utf-8">
<title>Field Bloom – Business Card</title>
<link href="https://fonts.googleapis.com/css2?family=Open+Sans:wght@400;600;700&display=swap" rel="stylesheet">
<style>
  :root {
    --backdrop: #2a2421;
    --card: #1b1b1d;
    --card-edge: #0f0f10;
    --gold: #d6ab45;
    --gold-light: #f1d27a;
    --gold-dark: #9c7424;
    --text-light: #e4e2de;
    --text-muted: #b9b6b0;
    --divider: #3a3a3d;
  }
  * { box-sizing: border-box; margin: 0; padding: 0; }
  html, body {
    width: 1200px; height: 844px; overflow: hidden;
    background: var(--backdrop);
    font-family: "Open Sans", sans-serif;
  }
  .stage {
    position: relative; width: 1200px; height: 844px;
    display: flex; align-items: center; justify-content: center; gap: 60px;
  }
  .card {
    position: relative; width: 520px; height: 297px;
    background: var(--card);
    border: 1px solid var(--card-edge);
    box-shadow: 0 12px 30px rgba(0,0,0,.45);
    overflow: hidden;
  }

  /* Front */
  .brand {
    position: absolute; left: 170px; top: 62px;
    display: flex; align-items: center; gap: 14px;
  }
  .brand-mark {
    width: 44px; height: 44px; border: 2px solid var(--gold);
  }
  .brand-text { display: flex; flex-direction: column; }
  .brand-name {
    color: var(--gold); font-weight: 700; font-size: 30px; line-height: 1;
  }
  .brand-url {
    color: var(--gold); font-weight: 400; font-size: 9px; margin-top: 6px; letter-spacing: .3px;
  }
  .identity {
    position: absolute; right: 262px; top: 170px; text-align: right;
  }
  .person-name { color: var(--gold); font-size: 20px; font-weight: 400; line-height: 1.1; }
  .person-role { color: var(--text-light); font-size: 13px; margin-top: 2px; }
  .address { color: var(--text-light); font-size: 13px; line-height: 1.3; margin-top: 14px; }
  .divider {
    position: absolute; left: 272px; top: 166px; width: 1px; height: 96px; background: var(--divider);
  }
  .contacts {
    position: absolute; left: 286px; top: 166px; list-style: none;
  }
  .contacts li {
    display: flex; align-items: center; gap: 9px;
    color: var(--text-light); font-size: 13px; line-height: 21px;
  }
  .contacts svg { width: 11px; height: 11px; fill: var(--gold); flex: none; }

  /* Back */
  .word-pattern {
    position: absolute; inset: 0;
    background: linear-gradient(135deg, #2b2a26 0%, #3a3326 45%, #2a2823 100%);
  }
  .back-name {
    position: absolute; right: 36px; bottom: 70px;
    color: var(--gold); font-weight: 700; font-size: 40px; line-height: 1;
  }
</style>
</head>
<body>
<main class="stage">

  <section class="card card-front" aria-label="Card front">
    <div class="brand">
      <span class="brand-mark"></span>
      <div class="brand-text">
        <span class="brand-name">Field Bloom</span>
        <span class="brand-url">www.fieldbloom.com</span>
      </div>
    </div>

    <div class="identity">
      <p class="person-name">Jonathan Smith</p>
      <p class="person-role">Managing Director</p>
      <p class="address">12345, Address Goes Here<br>Country Name, 123456</p>
    </div>

    <span class="divider"></span>

    <ul class="contacts">
      <li>
        <svg viewBox="0 0 12 12"><path d="M2.4 1h2l1 2.6-1.3 1a6.5 6.5 0 0 0 3.3 3.3l1-1.3L11 7.6v2c0 .8-.6 1.4-1.4 1.4A9.6 9.6 0 0 1 1 2.4C1 1.6 1.6 1 2.4 1z"/></svg>
        (044)-456-7890
      </li>
      <li>
        <svg viewBox="0 0 12 12"><path d="M4 2h4v1.5h2.5c.3 0 .5.2.5.5v6c0 .3-.2.5-.5.5h-9a.5.5 0 0 1-.5-.5V4c0-.3.2-.5.5-.5H4zm1 .8v.7h2v-.7z"/></svg>
        123-456-7890
      </li>
      <li>
        <svg viewBox="0 0 12 12"><path d="M1 2.5h10v7H1zm1 1v.3l4 2.6 4-2.6v-.3zm0 1.5v3.5h8V5L6 7.6z"/></svg>
        info@youremail.com
      </li>
      <li>
        <svg viewBox="0 0 12 12"><path d="M5 7 7 5M4.6 5.2 3 6.8a1.7 1.7 0 0 0 2.4 2.4L7 7.6M7.4 6.8 9 5.2A1.7 1.7 0 0 0 6.6 2.8L5 4.4" fill="none" stroke="#d6ab45" stroke-width="1.3" stroke-linecap="round"/></svg>
        www.website.com
      </li>
    </ul>
  </section>

  <section class="card card-back" aria-label="Card back">
    <div class="word-pattern" role="img" aria-label="Scattered gold foil words and symbols: Love, Peace, Namaste, inspire, live, Om, hearts and peace signs"></div>
    <p class="back-name">Field Bloom</p>
  </section>

</main>
</body>
</html>
```